Modern Business Card for Larkwell 2018

Our company assumes the best about people. We are creating an online community of entrepreneurs and business leaders who struggle with marketing their business online.

This business card should POP! We recently got a new logo and are launching a new website next month, so our business cards should make a statement that feels:
-Fresh
-Smart
-Trustworthy
-Fun

Target Market(s)

small business owners, entrepreneurs

Industry/Entity Type

Digital Marketing

Contact Information for Business Card

Dimensions: 3.5" x 2"

Font styles to use
Sans Serif

Colors
f37122
ffffff

Requirements
Must have
• We need a business card with a modern, bold design. We will use one side of the card as a lead-generation offer, so text on one side will need to fit up to 140 characters. The business card should stick to our core colors (orange, black, and white).
Nice to have
• We think a vertical "portrait" design could be interesting.
Should not have
• Should not look like a traditional business card. The round icon should stand out from a distance.

```html
<!DOCTYPE html>
<html lang="en">
<head>
<meta charset="utf-8">
<title>Larkwell Business Card</title>
<link href="https://fonts.googleapis.com/css2?family=Montserrat:wght@400;600;800&family=Caveat:wght@500&display=swap" rel="stylesheet">
<style>
  :root {
    --orange: #f37122;
    --white: #ffffff;
    --black: #111111;
    --ink: #1d1d1d;
    --backdrop: #e9e6e1;
    --silver-light: #f4f4f4;
    --silver-dark: #cfcfcf;
  }
  * { box-sizing: border-box; margin: 0; padding: 0; }
  html, body { width: 1200px; height: 911px; overflow: hidden; }
  body {
    background: var(--backdrop);
    font-family: "Montserrat", Arial, sans-serif;
    position: relative;
  }
  .card { position: absolute; overflow: hidden; box-shadow: 0 8px 24px rgba(0,0,0,.18); }

  /* Front: landscape contact card */
  .card-front {
    left: 70px; top: 295px; width: 560px; height: 320px;
    background: var(--white);
  }
  .front-corner { position: absolute; inset: 0; }
  .front-brand {
    position: absolute; right: 30px; top: 30px;
    font-weight: 800; font-size: 26px; letter-spacing: 2px; color: var(--white);
  }
  .contact { position: absolute; left: 36px; bottom: 34px; line-height: 1.15; }
  .contact-name { font-weight: 800; font-size: 26px; color: var(--ink); text-transform: uppercase; }
  .contact-role { font-weight: 600; font-size: 19px; color: var(--orange); text-transform: uppercase; }
  .contact-email { font-weight: 400; font-size: 18px; color: var(--ink); text-transform: uppercase; }

  /* Back: portrait lead-generation card */
  .card-back {
    left: 770px; top: 175px; width: 320px; height: 560px;
    background: var(--orange); color: var(--white);
    padding: 30px 22px 24px;
    display: flex; flex-direction: column; align-items: center;
  }
  .brand-lockup { display: flex; align-items: center; gap: 10px; }
  .brand-dot { width: 26px; height: 26px; border-radius: 50%; background: var(--white); flex: none; }
  .brand-name { font-weight: 800; font-size: 36px; letter-spacing: 1px; line-height: 1; }
  .tagline {
    font-family: "Caveat", cursive; font-size: 17px; letter-spacing: 1px;
    text-transform: uppercase; margin-top: 6px; white-space: nowrap;
  }
  .promise {
    margin-top: 12px; text-align: center;
    font-weight: 800; font-size: 18px; line-height: 1.15; text-transform: uppercase; letter-spacing: .5px;
  }
  .note-panel {
    margin-top: 14px; width: 100%; height: 196px; border-radius: 12px;
    background: linear-gradient(100deg, var(--silver-dark), var(--silver-light) 45%, var(--silver-dark));
    padding: 30px 18px 0;
  }
  .note-line { border-bottom: 1px dotted #555; height: 28px; }
  .offer {
    margin-top: 16px; text-align: center;
    font-weight: 400; font-size: 15px; line-height: 1.25; text-transform: uppercase; letter-spacing: .5px;
  }
  .offer strong { font-weight: 800; }
  .offer-link {
    margin-top: 12px; background: var(--black); color: var(--orange);
    font-weight: 800; font-size: 16px; padding: 6px 18px; border-radius: 20px;
  }
</style>
</head>
<body>
  <section class="card card-front" aria-label="Contact side">
    <svg class="front-corner" width="560" height="320" viewBox="0 0 560 320" aria-hidden="true">
      <polygon points="250,0 560,0 560,260" fill="#f37122"/>
    </svg>
    <div class="front-brand">LARKWELL</div>
    <div class="contact">
      <p class="contact-name">Dana Morrow</p>
      <p class="contact-role">Story Marketing Coach</p>
      <p class="contact-email">dana@larkwellnow.com</p>
    </div>
  </section>

  <section class="card card-back" aria-label="Offer side">
    <div class="brand-lockup">
      <span class="brand-dot"></span>
      <span class="brand-name">LARKWELL</span>
    </div>
    <p class="tagline">Tell stories that inspire action</p>
    <p class="promise">Reach more people.<br>Make more money.<br>Create more impact.</p>
    <div class="note-panel">
      <div class="note-line"></div>
      <div class="note-line"></div>
      <div class="note-line"></div>
      <div class="note-line"></div>
      <div class="note-line"></div>
    </div>
    <p class="offer">Get your free <strong>Larkwell</strong><br>starter package and our<br>marketing guide today at</p>
    <p class="offer-link">Larkwellnow.com/start</p>
  </section>
</body>
</html>
```